The most modern business card ever !!!

Our company call “Vendalo”. Vendalo is a technology company specialized in cruises solutions. Out main product is a platform to reserve cruises. This is a revolutionary platform that make easier to travel agencies and final users to reserve cruises across dozen companies like tibba, wernu, hpv, dgb, etc..We are a “start up”, with a young team of developers and we want to transmit it.. For it, we want something different, a modern business card that represent cruises and technology.. When someone receive this card, this person should say: wowww this is different… this is modern… this is a cruise related company..
- diferent, modern
- traditions business card

```html
<!DOCTYPE html>
<html lang="en">
<head>
<meta charset="utf-8">
<title>Vendalo – Business Card</title>
<link href="https://fonts.googleapis.com/css2?family=Roboto:wght@400;500;700&display=swap" rel="stylesheet">
<style>
  :root {
    --backdrop: #6f5637;
    --sky: #29a8e0;
    --ink: #000000;
    --paper: #ffffff;
    --frost: #9c8e7b;
  }
  * { margin: 0; padding: 0; box-sizing: border-box; }
  html, body {
    width: 1189px;
    height: 1200px;
    overflow: hidden;
    background: var(--backdrop);
    font-family: "Roboto", Arial, sans-serif;
  }
  .card {
    position: absolute;
    left: 353px;
    top: 178px;
    width: 482px;
    height: 845px;
    border-radius: 24px;
    overflow: hidden;
    display: flex;
    flex-direction: column;
  }
  .band-top { height: 32px; background: var(--sky); flex: none; }
  .brand-panel {
    height: 320px;
    background: var(--paper);
    flex: none;
    display: flex;
    align-items: center;
    justify-content: center;
    gap: 14px;
  }
  .brand-mark {
    width: 18px; height: 18px;
    background: var(--sky);
    flex: none;
  }
  .brand-name {
    font-size: 78px;
    font-weight: 500;
    color: var(--ink);
    letter-spacing: 2px;
    line-height: 1;
    margin-top: 12px;
  }
  .frost { height: 32px; background: var(--frost); flex: none; }
  .frost.lower { height: 31px; }
  .band-mid { height: 52px; background: var(--sky); flex: none; }
  .contact-panel {
    position: relative;
    height: 317px;
    background: var(--ink);
    flex: none;
    color: var(--paper);
    text-align: center;
  }
  .contact-panel > * {
    position: absolute;
    left: 0; right: 0;
    transform: translateY(-50%);
    line-height: 1.1;
  }
  .person-name { top: 51px; font-size: 29px; font-weight: 700; }
  .person-role { top: 77px; font-size: 23px; color: var(--sky); }
  .address-line { font-size: 21px; }
  .address-line.first { top: 114px; }
  .address-line.second { top: 142px; }
  .icon { display: block; margin: 0 auto; width: 31px; height: 31px; }
  .icon-phone { top: 181px; }
  .phone { top: 211px; font-size: 22px; }
  .divider {
    top: 230px;
    left: 103px; right: 103px;
    height: 1px;
    background: linear-gradient(90deg, transparent, #d8d8d8 20%, #d8d8d8 80%, transparent);
  }
  .icon-mail { top: 255px; }
  .email { top: 283px; font-size: 22px; }
  .rule-white { height: 10px; background: var(--paper); flex: none; }
  .band-web {
    height: 51px;
    background: var(--sky);
    flex: none;
    display: flex;
    align-items: center;
    justify-content: center;
    color: var(--paper);
    font-size: 20px;
    padding-bottom: 6px;
  }
</style>
</head>
<body>
  <div class="card">
    <div class="band-top"></div>
    <div class="brand-panel">
      <span class="brand-mark"></span>
      <span class="brand-name">Vendalo</span>
    </div>
    <div class="frost"></div>
    <div class="band-mid"></div>
    <div class="frost lower"></div>
    <div class="contact-panel">
      <p class="person-name">LENA MARSH</p>
      <p class="person-role">Founder</p>
      <p class="address-line first">PO BOX 123 your address</p>
      <p class="address-line second">2nd street Harbourton</p>
      <svg class="icon icon-phone" viewBox="0 0 32 32" aria-hidden="true">
        <circle cx="16" cy="16" r="14" fill="none" stroke="#29a8e0" stroke-width="2.5"/>
        <path d="M11.5 9.5c1-.6 1.8-.3 2.3.6l1 2c.4.8.2 1.4-.5 1.9l-.9.6c.6 1.8 1.9 3.3 3.6 4.2l.7-.8c.6-.6 1.2-.7 1.9-.3l1.9 1.2c.8.5 1 1.3.4 2.2-.9 1.4-2.3 1.9-3.9 1.2-3.8-1.6-6.5-4.9-7.5-8.8-.4-1.7.1-3.2 1-4z" fill="#29a8e0"/>
      </svg>
      <p class="phone">(123) 456-7890</p>
      <div class="divider"></div>
      <svg class="icon icon-mail" viewBox="0 0 32 32" aria-hidden="true">
        <circle cx="16" cy="16" r="14" fill="none" stroke="#29a8e0" stroke-width="2.5"/>
        <circle cx="16" cy="16" r="10.5" fill="#29a8e0"/>
        <rect x="10" y="12" width="12" height="8.5" fill="#000"/>
        <path d="M10 12l6 5 6-5M10 20.5l4.5-4M22 20.5l-4.5-4" fill="none" stroke="#29a8e0" stroke-width="1.2"/>
      </svg>
      <p class="email">info@companymail.com</p>
    </div>
    <div class="rule-white"></div>
    <div class="band-web">www.companyweb.com</div>
  </div>
</body>
</html>
```